Business Card Design for Software Development Company

I am looking for a business card design the incorporates my new logo (attached below).

Key information to include:
Name: Martin Quelbrook
Title: CEO
Email: martin@brightwellcivic.example
Phone: 555-218-9403
Website: www.brightwellcivic.example

NOTE: This design should be easy to edit so that we can order cards for different members of our team.

```html
<!DOCTYPE html>
<html lang="en">
<head>
<meta charset="utf-8">
<title>Brightwell Labs – Business Card</title>
<link href="https://fonts.googleapis.com/css2?family=Montserrat:wght@600;700&family=Poppins:wght@400;500;700&display=swap" rel="stylesheet">
<style>
  :root{
    --backdrop:#6a6a6c;
    --navy:#2f4659;
    --navy-light:#36536a;
    --ink:#2c3e50;
    --teal:#11a89a;
    --orange:#e8812a;
    --red:#c0392b;
    --white:#ffffff;
  }
  *{margin:0;padding:0;box-sizing:border-box}
  html,body{width:900px;height:1200px;overflow:hidden}
  body{background:var(--backdrop);position:relative;font-family:"Poppins",sans-serif}

  .card{position:absolute;left:135px;width:630px;height:360px}
  .card-front{top:213px;background:linear-gradient(90deg,var(--navy),var(--navy-light))}
  .card-back{top:627px;background:var(--white)}

  .wordmark{position:absolute;right:40px;text-align:right;font-family:"Montserrat",sans-serif}
  .wordmark-name{font-weight:700;letter-spacing:-0.5px;line-height:1}
  .wordmark-tag{font-weight:700;font-size:6px;letter-spacing:0.3px;margin-top:4px}

  .card-front .wordmark{bottom:36px;color:var(--white)}
  .card-front .wordmark-name{font-size:44px}
  .card-front .brand-square{position:absolute;left:42px;top:34px;width:26px;height:26px;background:var(--teal)}

  .card-back .wordmark{top:46px;color:var(--ink)}
  .card-back .wordmark-name{font-size:30px}

  .contact-block{position:absolute;left:44px;top:193px}
  .person-name{font-weight:700;font-size:24px;line-height:1.1;
    background:linear-gradient(180deg,var(--teal) 0 50%,var(--red) 50% 100%);
    -webkit-background-clip:text;background-clip:text;color:transparent}
  .person-title{font-size:14px;color:var(--ink);margin-top:2px}
  .title-rule{width:30px;height:2px;margin-top:4px;background:linear-gradient(90deg,var(--teal),var(--orange),var(--red))}
  .contact-list{list-style:none;margin-top:10px}
  .contact-list li{display:flex;align-items:center;gap:5px;font-size:15.5px;color:var(--ink);height:25px}
  .contact-list svg{width:15px;height:15px;flex:none}
  .phone{letter-spacing:3px;font-weight:500}
</style>
</head>
<body>

<section class="card card-front">
  <span class="brand-square"></span>
  <div class="wordmark">
    <div class="wordmark-name">Brightwell Labs</div>
    <div class="wordmark-tag">A DIVISION OF BRIGHTWELL CIVIC</div>
  </div>
</section>

<section class="card card-back">
  <div class="wordmark">
    <div class="wordmark-name">Brightwell Labs</div>
    <div class="wordmark-tag">A DIVISION OF BRIGHTWELL CIVIC</div>
  </div>

  <div class="contact-block">
    <h1 class="person-name">Martin Quelbrook</h1>
    <p class="person-title">CEO</p>
    <div class="title-rule"></div>
    <ul class="contact-list">
      <li>
        <svg viewBox="0 0 24 24" aria-hidden="true"><path fill="#c0392b" d="M6.6 10.8a15 15 0 0 0 6.6 6.6l2.2-2.2a1 1 0 0 1 1-.25 11.4 11.4 0 0 0 3.6.57 1 1 0 0 1 1 1V20a1 1 0 0 1-1 1A17 17 0 0 1 3 4a1 1 0 0 1 1-1h3.5a1 1 0 0 1 1 1c0 1.25.2 2.45.57 3.57a1 1 0 0 1-.25 1z"/></svg>
        <span class="phone">555-218-9403</span>
      </li>
      <li>
        <svg viewBox="0 0 24 24" aria-hidden="true"><rect x="2" y="5" width="20" height="14" fill="#e8812a"/><path d="M2 5l10 8 10-8" fill="none" stroke="#11a89a" stroke-width="2"/></svg>
        <span>martin@brightwellcivic.example</span>
      </li>
      <li>
        <svg viewBox="0 0 24 24" aria-hidden="true"><g fill="none" stroke="#c0392b" stroke-width="2"><circle cx="12" cy="12" r="9"/><ellipse cx="12" cy="12" rx="4" ry="9"/><path d="M3 12h18M5 7h14M5 17h14"/></g></svg>
        <span>www.brightwellcivic.example</span>
      </li>
    </ul>
  </div>
</section>

</body>
</html>
```